Wordpress Theme for Medical Clinics

** Please view updated Sitemap2.pdf doc to clarify some confusion ***

This is a multiuser WordPress subscription site for medical clinics. Please see attachment for sitemap. Please do not include extra content like social media icons, search bars, or images. If you have questions, please ask for clarification.
The site contains the following pages and sub-pages:

1. Home
2. Our Clinic
2a. Our Clinic > Mission
2b. Our Clinic > Services
2c. Our Clinic > Clinic Policies
2d. Our Clinic > Schedules
3. Our Staff
3a. Our Staff > [Staff member page]
4. Resources
4a. Resources > Patient Health (index)
4b. Resources > Patient Health (index) > [post]
4c. Resources > Links
4d. Resources > Forms
5. Alerts
5a. Alerts > [Alert Page]
6. Contact Us

Includes the Following Pages, Subpages, and Content
1. Home
a. About Us
b. Our Staff
c. Bulletins
d. Accepting New Patients (shown as an alert widget)
e. Links
i. Physician Toolbox
ii. Book an Appointment
f. Clinic Policies
i. Show first 3 policies (e.g. Late Arrivals, Missed Appointments, Fees)
ii. Link to Clinic Policies page
g. Primary widget (displayed on all pages)
i. Hours of operation
ii. Contact Info
1. Tel
2. Fax
3. Email
4. Address
5. Get directions (link to Google Maps)
2. Our Clinic
a. Main Page
i. Clinic Name
ii. Overview
iii. Languages Spoken
iv. Secondary Navigation
1. Mission
2. Services
3. Clinic Policies
4. Schedules (see attachment)
b. Our Clinic > Mission
c. Our Clinic > Services
i. For each service include service TITLE and DESCRIPTION
d. Our Clinic > Clinic Policies
i. For each policy include policy TITLE and DESCRIPTION
ii. Include the following policies in mockup
1. Late arrivals
2. Missed appointments
3. Fees for missed appointments
4. Referrals and follow-ups
5. Services not covered by RDA
6. Information for LTF patients
7. Medical Legal Reports
e. Our Clinic > Schedules
3. Our Staff
a. Main Page
i. Display a list of staff members. Include NAME and DESIGNATION
b. Our Staff > [Staff Name]
i. Include NAME, PICTURE, DESIGNATION, and BIO
4. Resources
a. Resources > Patient Health
i. Main Page
1. Posts (ordered by date)
a. Title
b. Summary
2. Side Navigation
a. Post Categories
ii. Patient Health > [post title]
1. Title
2. Post Category
3. Date
4. Author
5. Summary
6. Body
b. Resources > Links
1. Secondary Navigation - Categories
a. Sample Categories:
i. Local Services
ii. RDA and Drug Coverage
iii. Mental Health Resources
2. Category page
a. Include the following links in the 'Local Services' category
i. Hypertension clinics
ii. Home Care services
iii. Vaccine Clinics
c. Resources > Forms
i. Display a table with form TITLE and CATEGORY
ii. Side Navigation
1. Form Categories
a. Use the following sample Categories
i. Referrals
ii. Insurance
iii. Intake
iv. Discharge
v. Waivers
5. Alerts
a. Main page
i. List of all Alert posts
1. Include post TITLE as a link to the post
ii. Side Navigation
1. Alerts Archive
a. shown as Month + Number of posts
iii. Alerts > [Alert page]
1. Include TITLE, DATE, AUTHOR, BODY
6. Contact Us
a. Map
b. Hours of operation
c. Address
d. Phone number
e. Fax number
e. Fax number
f. Map
g. Email

Design notes:
- fixed width
- responsive (need designs for mobile, tablet, and desktop)
- simple, dark font, white background
- use Font Awesome icons where needed
- user adds own logo

Target Market(s)

Medical Clinics

Industry/Entity Type

Medical

Number of Pages Required

5+ page

Font styles to use
Serif
Sans Serif

Requirements
Must have
• Please keep designs very simple.
• Examples:
• https://www.quolbin.com/install
• http://www.ventrohax.com/company/about-us
• http://brindlequota.org/
• http://www.trosk.com/
Should not have
• Minimal or no use of shadows and gradients

```html
<!DOCTYPE html>
<html lang="en">
<head>
<meta charset="utf-8">
<title>Medical – Services</title>
<link rel="stylesheet" href="https://fonts.googleapis.com/css2?family=Open+Sans:wght@300;400;600;700&display=swap">
<style>
:root{
  --blue:#1a7bc4;
  --page:#ececec;
  --white:#ffffff;
  --ink:#2b2b2b;
  --muted:#7a7f87;
  --body:#6b7480;
  --rule:#e3e5e8;
  --foot:#333436;
  --foot-bottom:#2b2c2e;
  --foot-text:#c9cbce;
}
*{box-sizing:border-box;margin:0;padding:0}
html,body{width:1000px;height:1200px;overflow:hidden}
body{background:var(--page);font-family:"Open Sans",Arial,sans-serif;color:var(--ink);position:relative}
.site{position:absolute;left:23px;top:0;width:956px;height:1200px;background:var(--white)}
.abs{position:absolute}
a{color:inherit;text-decoration:none}

/* top bar */
.topbar{left:0;top:0;width:956px;height:26px;border-top:2px solid var(--blue);border-bottom:1px solid var(--rule);font-size:8px;color:var(--muted)}
.topbar .call{left:69px;top:6px}
.topbar .call b{font-weight:600;color:#555}
.topbar .links{right:70px;top:6px;display:flex;gap:24px;align-items:center}
.topbar .links span{display:flex;align-items:center;gap:5px}

/* header */
.brand{display:flex;align-items:center;gap:8px;font-size:21px;font-weight:400;color:var(--ink)}
.brand .dot{width:34px;height:34px;border-radius:50%;background:var(--blue)}
.header-brand{left:69px;top:40px}
.nav-link{position:absolute;top:48px;font-size:11.5px;color:var(--ink);white-space:nowrap}
.nav-link.active{color:var(--blue)}
.nav-bar{left:528px;top:25px;width:32px;height:2px;background:var(--blue)}

/* title bar */
.titlebar{left:0;top:90px;width:956px;height:120px;background:linear-gradient(#f1f2f4,#ffffff)}
.pagetitle{left:67px;top:107px;font-size:16.5px;font-weight:300;color:var(--blue);padding-bottom:13px;border-bottom:2px solid var(--blue);width:65px;white-space:nowrap}
.crumbs{left:156px;top:113px;font-size:8.5px;color:var(--muted)}
.crumbs u{text-decoration:underline}
.titlerule{left:67px;top:144px;width:821px;height:1px;background:var(--rule)}

/* sidebar */
.side{left:68px;top:170px;width:193px}
.side h3{font-size:12.5px;font-weight:400;margin-bottom:10px}
.side li{list-style:none;display:flex;align-items:center;gap:8px;height:28px;border-bottom:1px solid #eef0f2;font-size:9px;color:var(--muted)}
.side li .ring{width:13px;height:13px;border:1px solid #9aa0a6;border-radius:50%;display:flex;align-items:center;justify-content:center;font-size:8px}
.side li.on{color:var(--blue)}
.side li.on .ring{background:var(--blue);border-color:var(--blue);color:#fff}

/* content */
.content-title{left:297px;top:178px;font-size:24px;font-weight:300}
.content-rule{left:297px;top:222px;width:526px;height:1px;background:var(--rule)}
.content-rule::before{content:"";position:absolute;left:0;top:-1px;width:53px;height:2px;background:var(--blue)}
.service{left:295px;width:526px}
.service h2{display:flex;align-items:center;gap:8px;font-size:16.5px;font-weight:400;margin-bottom:17px}
.service .icon{width:32px;height:32px;background:var(--blue);display:flex;align-items:center;justify-content:center}
.service p{font-size:9px;line-height:14px;color:var(--body);padding-left:2px}
.service .end{height:1px;width:502px;background:var(--blue);opacity:.7}

/* footer */
.footer{left:0;top:841px;width:956px;height:307px;background:var(--foot);color:var(--foot-text);font-size:9px}
.footer .brand{color:#fff;font-size:20px}
.fcol{position:absolute}
.fcol h4{color:#fff;font-size:10px;font-weight:600;margin-bottom:20px}
.fcol ul{list-style:none}
.arrow::before{content:"›";margin-right:8px;color:#fff;font-size:12px}
.clinic-links li{color:#fff;font-size:10px;height:21px}
.tweet{margin-bottom:18px;display:flex;gap:6px;line-height:15px}
.tweet b{color:#fff;font-weight:600}
.tweet small{display:block;color:#3a97e0;font-size:8px;margin-top:3px}
.contact-row{display:flex;gap:12px;line-height:15px;margin-bottom:15px}
.subscribe{display:flex;margin-top:12px;height:21px}
.subscribe input{width:125px;border:0;background:#f4f4f4;font:8.5px "Open Sans",sans-serif;padding-left:8px;color:#999}
.subscribe button{width:61px;border:0;background:var(--blue);color:#fff;font:9px "Open Sans",sans-serif}
.copy{left:0;top:1148px;width:956px;height:52px;background:var(--foot-bottom);color:var(--foot-text);font-size:8.5px;padding:20px 0 0 69px}
</style>
</head>
<body>
<div class="site">

  <div class="abs topbar">
    <div class="abs call"><b>Call Us Today!</b>&nbsp; +100 482 317 &nbsp;&nbsp;|&nbsp;&nbsp; contact@alderclinic.test</div>
    <div class="abs links">
      <span><svg width="9" height="11" viewBox="0 0 9 11"><rect x="0.5" y="1.5" width="8" height="9" fill="none" stroke="#9aa0a6"/><rect x="2.5" y="0.5" width="4" height="2" fill="#9aa0a6"/></svg>Book an Appointment</span>
      <span style="color:#ccc">|</span>
      <span><svg width="12" height="10" viewBox="0 0 12 10"><rect x="0.5" y="2.5" width="11" height="7" fill="none" stroke="#9aa0a6"/><rect x="4" y="0.5" width="4" height="2" fill="none" stroke="#9aa0a6"/><path d="M6 4v4M4 6h4" stroke="#9aa0a6"/></svg>Physician Toolbox</span>
    </div>
  </div>

  <div class="abs brand header-brand"><span class="dot"></span>Medical</div>
  <nav>
    <div class="abs nav-bar"></div>
    <a class="nav-link active" href="#" style="left:529px">Home</a>
    <a class="nav-link" href="#" style="left:588px">Our Clinic</a>
    <a class="nav-link" href="#" style="left:665px">Staff</a>
    <a class="nav-link" href="#" style="left:713px">Resources</a>
    <a class="nav-link" href="#" style="left:792px">Alerts</a>
    <a class="nav-link" href="#" style="left:847px">Contact</a>
  </nav>

  <div class="abs titlebar"></div>
  <div class="abs pagetitle">Our clinic</div>
  <div class="abs crumbs"><u>Home</u> &nbsp;›&nbsp; Our Clinic</div>
  <div class="abs titlerule"></div>

  <aside class="abs side">
    <h3>Categories</h3>
    <ul>
      <li><span class="ring">›</span>Overview</li>
      <li><span class="ring">›</span>Mission</li>
      <li class="on"><span class="ring">›</span>Services</li>
      <li><span class="ring">›</span>Schedules</li>
      <li><span class="ring">›</span>Clinic Policies</li>
    </ul>
  </aside>

  <h1 class="abs content-title">Services</h1>
  <div class="abs content-rule"></div>

  <section class="abs service" style="top:285px">
    <h2><span class="icon"><svg width="14" height="13" viewBox="0 0 14 13"><path d="M7 12.5 1.3 6.8A3.4 3.4 0 0 1 7 2.4a3.4 3.4 0 0 1 5.7 4.4z" fill="#fff"/></svg></span>Heart Disease</h2>
    <p>Integer iaculis egestas odio, vel dictum turpis placerat id ellentesque semper nisl eget odio eleifend, nec blandit libero porta aliquam vel vehicula dui nam sit amet ultricies sapien.<br>Nulla euismod vitae justo a ullamcorper. In rhoncus nisi massa, sit amet tristique augue viverra vitae. Ut vitae lectus quam.<br>Proin aliquet rhoncus magna vel scelerisque. Nulla facilisi. Aliquam ut scelerisque nulla.</p>
    <div class="end" style="margin-top:14px"></div>
  </section>

  <section class="abs service" style="top:441px">
    <h2><span class="icon"><svg width="16" height="11" viewBox="0 0 16 11"><rect x="0" y="1" width="10" height="7" fill="#fff"/><path d="M10 3h3l3 3v2h-6z" fill="#fff"/><circle cx="3.5" cy="9" r="1.8" fill="#fff"/><circle cx="12.5" cy="9" r="1.8" fill="#fff"/><path d="M5 2.5v4M3 4.5h4" stroke="#1a7bc4" stroke-width="1.3"/></svg></span>Yellow Fever</h2>
    <p>Integer iaculis egestas odio, vel dictum turpis placerat id ellentesque semper nisl eget odio eleifend, nec blandit libero porta aliquam vel vehicula dui nam sit amet ultricies sapien.<br>Nulla euismod vitae justo a ullamcorper. In rhoncus nisi massa, sit amet tristique augue viverra vitae. Ut vitae lectus quam.<br>Proin aliquet rhoncus magna vel scelerisque. Nulla facilisi. Aliquam ut scelerisque nulla.</p>
    <div class="end" style="margin-top:18px"></div>
  </section>

  <section class="abs service" style="top:607px">
    <h2><span class="icon"><svg width="14" height="13" viewBox="0 0 14 13"><path d="M7 12.5 1.3 6.8A3.4 3.4 0 0 1 7 2.4a3.4 3.4 0 0 1 5.7 4.4z" fill="#fff"/></svg></span>Heart Disease</h2>
    <p>Integer iaculis egestas odio, vel dictum turpis placerat id ellentesque semper nisl eget odio eleifend, nec blandit libero porta aliquam vel vehicula dui nam sit amet ultricies sapien.<br>Nulla euismod vitae justo a ullamcorper. In rhoncus nisi massa, sit amet tristique augue viverra vitae. Ut vitae lectus quam.<br>Proin aliquet rhoncus magna vel scelerisque. Nulla facilisi. Aliquam ut scelerisque nulla.</p>
    <p style="margin-top:5px">Integer iaculis egestas odio, vel dictum turpis placerat id ellentesque semper nisl eget odio eleifend, nec blandit libero porta aliquam vel vehicula dui nam sit amet ultricies sapien.<br>Nulla euismod vitae justo a ullamcorper. In rhoncus nisi massa, sit amet tristique augue viverra vitae. Ut vitae lectus quam.<br>Proin aliquet rhoncus magna vel scelerisque. Nulla facilisi. Aliquam ut scelerisque nulla.</p>
    <div class="end" style="margin-top:26px"></div>
  </section>

  <footer class="abs footer">
    <div class="fcol" style="left:69px;top:41px;width:160px">
      <div class="brand"><span class="dot"></span>Medical</div>
      <p style="margin:15px 0 18px;line-height:15px">Lorem ipsum dolor sit amet, teft consecte tur adipiscing.</p>
      <div class="contact-row"><svg width="9" height="12" viewBox="0 0 9 12"><path d="M4.5 12S0 6.5 0 4.5a4.5 4.5 0 0 1 9 0C9 6.5 4.5 12 4.5 12z" fill="#c9cbce"/><circle cx="4.5" cy="4.5" r="1.6" fill="#333436"/></svg><div style="margin-left:2px">Medical Clinic<br>48 Alder Lane<br>Brookvale, NY 10160</div></div>
      <div class="contact-row" style="margin-top:0"><svg width="10" height="26" viewBox="0 0 10 26"><path d="M1 1h3l1 3-2 1a6 6 0 0 0 3 3l1-2 3 1v3C4 10 1 6 1 1z" fill="#c9cbce"/><rect x="1" y="19" width="8" height="5" fill="#c9cbce"/><rect x="3" y="16" width="4" height="3" fill="#c9cbce"/></svg><div>+100 482 317<br>+100 482 318</div></div>
      <div class="contact-row"><svg width="10" height="8" viewBox="0 0 10 8"><rect width="10" height="8" fill="#c9cbce"/><path d="M0 0l5 4 5-4" stroke="#333436" fill="none"/></svg><div style="color:#fff">contact@alderclinic.test</div></div>
    </div>

    <div class="fcol" style="left:273px;top:51px">
      <h4 style="margin-bottom:17px">OUR CLINIC</h4>
      <ul class="clinic-links">
        <li class="arrow">Mission</li><li class="arrow">Services</li><li class="arrow">Schedules</li><li class="arrow">Policies</li><li class="arrow">More</li>
      </ul>
    </div>

    <div class="fcol" style="left:478px;top:51px;width:180px">
      <h4 style="margin-bottom:18px">RESOURCES</h4>
      <div class="tweet"><span style="color:#fff">›</span><div>Integer iaculis egestas odio, vel dictum turpis placerat id. Pellentesque semper nisl eget: <b>lnk.test/Rk4Toudq</b><small>2 days ago</small></div></div>
      <div class="tweet"><span style="color:#fff">›</span><div>Curabitur consequat tortor ut eros posu ere rutrum donec metus nisl, dictum vita fermentum: <b>lnk.test/Rk4Toudq</b><small>6 days ago</small></div></div>
    </div>

    <div class="fcol" style="left:683px;top:51px;width:190px">
      <h4 style="margin-bottom:18px">NEWSLETTER</h4>
      <p style="line-height:15px">Ipsum dolor sit amet, teft consecte tur adipiscing elit ut eunt.</p>
      <div class="subscribe"><input value="Email Address" aria-label="Email Address"><button>Subscribe</button></div>
    </div>
  </footer>

  <div class="abs copy">Copyright 2015 Medical | All Rights Reserved</div>
</div>
</body>
</html>
```